Keystone Trench Co Business Card*

Looking for a professional, clean and crisp business card

I am in the underground utilities industry and am just looking for a really impressive business card. I would like our card to be white with our symbol crisp and clear with it protruding. I also have a business partner that will require his name and info on the card once the design is set. I would like to have our website info on the card which is;
http://keystonetrenchco.example/

Contact Information for Business Card

Website, contact name, number and email

```html
<!DOCTYPE html>
<html lang="en">
<head>
<meta charset="utf-8">
<title>Keystone Trench Co — Business Cards</title>
<link rel="stylesheet" href="https://fonts.googleapis.com/css2?family=Lato:wght@400;700;900&display=swap">
<style>
  :root {
    --stage: #2b2b2c;
    --card-white: #ffffff;
    --card-black: #1c1a1b;
    --card-black-soft: #2a2627;
    --ink: #111111;
    --ink-muted: #6b6b6b;
    --accent-blue: #3f5fae;
    --rule-blue: #9aaad6;
    --mark-red: #c8202a;
    --paper-text: #ffffff;
  }
  * { box-sizing: border-box; margin: 0; padding: 0; }
  html, body {
    width: 1200px; height: 2211px; overflow: hidden;
    background: var(--stage);
    font-family: "Lato", Arial, sans-serif;
  }
  .sheet {
    width: 1200px; height: 2211px;
    display: grid; grid-template-rows: 1105px 1106px;
  }
  .card-set {
    position: relative;
    display: flex; justify-content: center; align-items: center; gap: 60px;
  }
  .card {
    width: 350px; height: 600px; border-radius: 22px;
    box-shadow: 0 18px 40px rgba(0,0,0,.45);
    position: relative; overflow: hidden;
  }
  .card--front {
    background: var(--card-white);
    display: flex; flex-direction: column; align-items: center;
    padding-top: 120px; color: var(--ink);
  }
  .brand {
    display: flex; align-items: center; gap: 12px;
    font-weight: 900; font-size: 25px; letter-spacing: .5px;
    text-transform: uppercase; color: var(--ink);
  }
  .brand__dot {
    width: 18px; height: 18px; border-radius: 50%;
    background: var(--accent-blue); flex: none;
  }
  .person__name {
    margin-top: 120px; font-weight: 900; font-size: 30px; color: var(--ink);
  }
  .person__role {
    margin-top: 2px; font-size: 17px; color: var(--ink-muted);
  }
  .contact-rule {
    margin-top: 14px; width: 180px; position: relative;
    display: flex; justify-content: center; gap: 4px;
  }
  .contact-rule::before {
    content: ""; position: absolute; left: 0; right: 0; top: 50%;
    height: 1px; background: var(--rule-blue);
  }
  .contact-icon {
    position: relative; width: 18px; height: 18px; border-radius: 50%;
    background: var(--accent-blue); display: flex; align-items: center; justify-content: center;
  }
  .contact-icon svg { width: 11px; height: 11px; }
  .contact-list {
    list-style: none; margin-top: 14px; text-align: center;
    font-size: 17px; line-height: 1.55; color: var(--ink-muted);
  }
  .card--back {
    background: var(--card-black);
  }
  .back__texture {
    position: absolute; inset: 0;
    background: linear-gradient(160deg, var(--card-black-soft) 0%, var(--card-black) 75%);
  }
  .back__brand {
    position: absolute; left: 0; right: 0; bottom: 90px;
    display: flex; justify-content: center; align-items: center; gap: 10px;
    font-weight: 900; font-size: 24px; letter-spacing: .5px;
    text-transform: uppercase; color: var(--paper-text);
  }
</style>
</head>
<body>
<main class="sheet">

  <section class="card-set">
    <article class="card card--front">
      <div class="brand"><span class="brand__dot"></span>Keystone Trench Co</div>
      <h1 class="person__name">Dale Merriton</h1>
      <p class="person__role">Owner</p>
      <div class="contact-rule">
        <span class="contact-icon"><svg viewBox="0 0 12 12"><path d="M3 1.5l1.6 2.2-1 1.1a6 6 0 0 0 3.6 3.6l1.1-1 2.2 1.6-.8 1.5C5.5 10.5 1.5 6.5 1.5 2.3z" fill="#fff"/></svg></span>
        <span class="contact-icon"><svg viewBox="0 0 12 12"><rect x="1.5" y="3" width="9" height="6" fill="none" stroke="#fff" stroke-width="1"/><path d="M1.5 3l4.5 3.5L10.5 3" fill="none" stroke="#fff" stroke-width="1"/></svg></span>
        <span class="contact-icon"><svg viewBox="0 0 12 12"><circle cx="6" cy="6" r="4.5" fill="none" stroke="#fff" stroke-width="1"/><ellipse cx="6" cy="6" rx="2" ry="4.5" fill="none" stroke="#fff" stroke-width="1"/><path d="M1.5 6h9" stroke="#fff" stroke-width="1"/></svg></span>
      </div>
      <ul class="contact-list">
        <li>555-010-3447 (DIGS)</li>
        <li>Dale@keystonetrenchco.example</li>
        <li>www.keystonetrenchco.example</li>
      </ul>
    </article>
    <article class="card card--back">
      <div class="back__texture" role="img" aria-label="Faint repeating company wordmark texture"></div>
      <div class="back__brand">Keystone Trench Co</div>
    </article>
  </section>

  <section class="card-set">
    <article class="card card--front">
      <div class="brand"><span class="brand__dot"></span>Keystone Trench Co</div>
      <h1 class="person__name">Evan Holbrook</h1>
      <p class="person__role">Owner</p>
      <div class="contact-rule">
        <span class="contact-icon"><svg viewBox="0 0 12 12"><path d="M3 1.5l1.6 2.2-1 1.1a6 6 0 0 0 3.6 3.6l1.1-1 2.2 1.6-.8 1.5C5.5 10.5 1.5 6.5 1.5 2.3z" fill="#fff"/></svg></span>
        <span class="contact-icon"><svg viewBox="0 0 12 12"><rect x="1.5" y="3" width="9" height="6" fill="none" stroke="#fff" stroke-width="1"/><path d="M1.5 3l4.5 3.5L10.5 3" fill="none" stroke="#fff" stroke-width="1"/></svg></span>
        <span class="contact-icon"><svg viewBox="0 0 12 12"><circle cx="6" cy="6" r="4.5" fill="none" stroke="#fff" stroke-width="1"/><ellipse cx="6" cy="6" rx="2" ry="4.5" fill="none" stroke="#fff" stroke-width="1"/><path d="M1.5 6h9" stroke="#fff" stroke-width="1"/></svg></span>
      </div>
      <ul class="contact-list">
        <li>555-011-3447 (DIGS)</li>
        <li>Evan@keystonetrenchco.example</li>
        <li>www.keystonetrenchco.example</li>
      </ul>
    </article>
    <article class="card card--back">
      <div class="back__texture" role="img" aria-label="Faint repeating company wordmark texture"></div>
      <div class="back__brand">Keystone Trench Co</div>
    </article>
  </section>

</main>
</body>
</html>
```